Brivo Australia Dental

I need to update my website and design. I have some ideas in mind and would like to replicate the format from another website into my own. I need the website to be easy to edit (I have no prior wordpress exp) after the design is complete. Please visit https://thelittlenestcare.org.au/ for example of layout.
Target Market(s)
Parents and elder folks
Industry/Entity Type
Dental
Coding
Coded - Design and coding required
Number of Pages Required
4 page
Font styles to use
Sans Serif
Colors
0392cd
Requirements
Must have
- - Home, Services, About Us, News
- - Colours
- - Clear action from viewers
- - Location of business (able to change all the time)
- - Illustrations/ photos

```html
<!DOCTYPE html>
<html lang="en">
<head>
<meta charset="utf-8">
<title>Brivo Australia Dental</title>
<link href="https://fonts.googleapis.com/css2?family=Rubik:wght@500;700&family=Lato:wght@400;700&family=Roboto:wght@400;500&display=swap" rel="stylesheet">
<style>
:root{
  --brand:#0392cd;
  --brand-light:#2ab0ea;
  --ring:#49c2f2;
  --band:#1f9ad6;
  --ink:#1a1a1a;
  --text:#555;
  --black:#000;
  --white:#fff;
}
*{box-sizing:border-box;margin:0;padding:0}
html,body{width:1200px;height:3558px;overflow:hidden}
body{position:relative;font-family:'Lato',sans-serif;color:var(--text);background:var(--white)}
.abs{position:absolute}
.topbar{left:0;top:0;width:1200px;height:37px;background:var(--band);color:var(--white);font-size:14px}
.topbar .addr{left:90px;top:10px;display:flex;gap:8px;align-items:center}
.topbar .social{right:90px;top:9px;display:flex;gap:12px}
.topbar .social span{width:20px;height:20px;border-radius:50%;background:var(--white);display:block}
.header{left:0;top:37px;width:1200px;height:90px}
.logo{left:90px;top:14px;font-family:'Lato',sans-serif;font-weight:700;font-size:40px;color:var(--brand);letter-spacing:1px}
.phone{left:712px;top:23px;font-family:'Roboto',sans-serif;font-weight:500;font-size:29px;color:#444;display:flex;align-items:center;gap:10px}
.book{left:958px;top:24px;width:151px;height:39px;background:var(--brand-light);color:var(--white);font-family:'Roboto',sans-serif;font-size:18px;display:flex;align-items:center;justify-content:center}
.nav{left:0;top:127px;width:1200px;height:46px;background:var(--black);font-family:'Roboto',sans-serif;font-size:17px;color:var(--white)}
.nav a{position:absolute;top:13px;color:var(--white);text-decoration:none}
.nav a.active{border-bottom:2px solid var(--white);padding:0 8px 10px}
.hero{left:0;top:173px;width:1200px;height:583px;background:linear-gradient(100deg,#33443f 0%,#5b6a63 35%,#a98a78 60%,#6d7a75 100%)}
.hero h1{position:absolute;left:90px;top:190px;font-family:'Rubik',sans-serif;font-weight:700;font-size:56px;color:var(--white);letter-spacing:1px}
.hero p{position:absolute;left:90px;top:253px;width:380px;font-size:18px;line-height:27px;color:var(--white)}
.btn{background:linear-gradient(#2ab3ee,#0b8fd0);color:var(--white);font-family:'Roboto',sans-serif;font-size:21px;display:flex;align-items:center;justify-content:center}
.hero .btn{position:absolute;left:90px;top:335px;width:202px;height:52px}
.title{left:0;width:1200px;text-align:center;font-family:'Rubik',sans-serif;font-weight:700;font-size:36px;color:var(--brand)}
.lead{text-align:center;font-size:17.5px;line-height:27px}
.photo{border-radius:50%;border:7px solid var(--ring)}
.h3{text-align:center;font-family:'Rubik',sans-serif;font-weight:500;font-size:22px;color:var(--ink)}
.body{text-align:center;font-size:16px;line-height:32px;color:#666}
.about{left:0;top:1562px;width:1200px;height:628px;background:linear-gradient(120deg,#1792d3,#21a2de 60%,#1b95d5)}
.about .title{color:var(--white);top:52px}
.about .lead{position:absolute;left:140px;top:115px;width:920px;color:var(--white);font-size:16.5px;line-height:32px}
.about .photo{border:none}
.about .label{position:absolute;top:548px;width:300px;text-align:center;font-family:'Rubik',sans-serif;font-weight:700;font-size:23px;color:var(--white)}
.map{left:0;top:2873px;width:1200px;height:557px;background:linear-gradient(135deg,#eef0f2,#e3e6e9 50%,#eceef0)}
.contact-frame{left:98px;top:3048px;width:356px;height:242px;border:2px solid #111}
.contact{left:108px;top:3062px;width:335px;height:210px;background:var(--brand);color:var(--white);padding:24px 32px;font-size:14.5px}
.contact h4{font-family:'Rubik',sans-serif;font-weight:700;font-size:17px;margin-bottom:12px}
.contact li{list-style:none;display:flex;gap:12px;margin-bottom:7px;line-height:20px}
.contact svg{flex:none;margin-top:3px}
.footer{left:0;top:3430px;width:1200px;height:128px;background:var(--black);color:var(--white);text-align:center;font-size:18px}
.footer nav{position:absolute;top:37px;width:1200px;display:flex;justify-content:center;gap:33px}
.footer p{position:absolute;top:80px;width:1200px;font-size:16px}
</style>
</head>
<body>

<div class="abs topbar">
  <div class="abs addr">
    <svg width="18" height="16" viewBox="0 0 18 16"><path d="M9 1a4 4 0 0 0-4 4c0 3 4 7 4 7s4-4 4-7a4 4 0 0 0-4-4zm0 5.5a1.5 1.5 0 1 1 0-3 1.5 1.5 0 0 1 0 3zM1 9l4-1v7l-4 1zM13 8l4 1v6l-4-1z" fill="#fff"/></svg>
    27 Kessel St, Marlow NSW 2600, Australia
  </div>
  <div class="abs social" aria-label="Social links"><span></span><span></span><span></span><span></span><span></span></div>
</div>

<header class="abs header">
  <div class="abs logo">Brivo</div>
  <div class="abs phone">
    <svg width="16" height="16" viewBox="0 0 24 24"><path d="M6.6 10.8a15 15 0 0 0 6.6 6.6l2.2-2.2c.3-.3.7-.4 1-.2 1.1.4 2.3.6 3.6.6.6 0 1 .4 1 1V20c0 .6-.4 1-1 1A17 17 0 0 1 3 4c0-.6.4-1 1-1h3.5c.6 0 1 .4 1 1 0 1.3.2 2.5.6 3.6.1.3 0 .7-.2 1z" fill="#0392cd"/></svg>
    1300 555 014
  </div>
  <div class="abs book">BOOK NOW</div>
</header>

<nav class="abs nav">
  <a class="active" style="left:285px">HOME</a>
  <a style="left:423px">SERVICES</a>
  <a style="left:582px">ABOUT US</a>
  <a style="left:745px">NEWS</a>
  <a style="left:875px">CONTACT US</a>
</nav>

<section class="abs hero" role="img" aria-label="Dentist examining a smiling patient in the chair">
  <h1>BRIVO-DENTAL</h1>
  <p>Brivo Mobile Dental is a group of Dental Professionals who strongly believes anyone.</p>
  <div class="btn">GET A STARTED</div>
</section>

<h2 class="abs title" style="top:810px">OUR SERVICES</h2>
<p class="abs lead" style="left:150px;top:868px;width:900px">Brivo Mobile Dental is a group of Dental Professionals who strongly believes anyone and anywhere can look healthy and fabulous with a bright Smile</p>

<div class="abs photo" style="left:203px;top:951px;width:268px;height:268px;background:linear-gradient(135deg,#2a3a3a,#7b8f8a 50%,#b89a70)" role="img" aria-label="Colouring pencils on an open children's book"></div>
<div class="abs photo" style="left:709px;top:951px;width:268px;height:268px;background:linear-gradient(135deg,#c9c3bb,#8d8983 50%,#e6e2dc)" role="img" aria-label="Striped cushion on a bed"></div>

<h3 class="abs h3" style="left:137px;top:1244px;width:400px">GROW TO SMILE PROGRAM</h3>
<p class="abs body" style="left:145px;top:1290px;width:382px;text-align:justify;text-align-last:center">Our Mobile Services Are Performed Within The Spacious Compounds Of &nbsp;Our State Of The Art Mobile Clinic Educational Presentations And Seminars For Kids And Parents To Enjoy</p>
<div class="abs btn" style="left:254px;top:1448px;width:166px;height:51px">READ MORE</div>

<h3 class="abs h3" style="left:643px;top:1244px;width:400px">BEAUTIFUL &amp; RETIRED PROGRAM</h3>
<p class="abs body" style="left:652px;top:1290px;width:382px;text-align:justify;text-align-last:center">Our mobile services are performed within the spacious compounds of our State of the Art Mobile clinicEducational presentations Seminars to retirement homes and villages</p>
<div class="abs btn" style="left:747px;top:1448px;width:166px;height:51px">READ MORE</div>

<section class="abs about">
  <h2 class="abs title">ABOUT US</h2>
  <p class="lead">Lorem ipsum dolor sit amet, consectetur adipiscing elit. Ut at velit tristique, vehicula sapien quis, tristique est. Cras pellentesque est non sem consectetur, in volutpat ex auctor. Vivamus consectetur eget lorem ut euismod. Aenean blandit eget quam id placerat. Morbi felis massa, sodales eu porttitor ut, malesuada tempor ex. Nunc sagittis consequat odio, vel ultrices eros pharetra feugiat.</p>
  <div class="abs photo" style="left:163px;top:298px;width:220px;height:220px;background:linear-gradient(135deg,#f3f6f8,#cdd6dc 60%,#8c979e)" role="img" aria-label="Bright dental surgery with treatment chair"></div>
  <div class="abs photo" style="left:475px;top:298px;width:220px;height:220px;background:linear-gradient(180deg,#a9c9e0,#6f8f66 45%,#c9b49b 60%,#5b97b8)" role="img" aria-label="Lakeside town with villas and boats"></div>
  <div class="abs photo" style="left:812px;top:298px;width:220px;height:220px;background:linear-gradient(135deg,#3a3d45,#6b6f76 50%,#2f8a3a)" role="img" aria-label="Child drawing with a green marker"></div>
  <div class="label" style="left:123px">PROFESSIONALISM</div>
  <div class="label" style="left:435px">HONESTY</div>
  <div class="label" style="left:772px">EDUCATION</div>
</section>

<h2 class="abs title" style="top:2242px">WHAT MAKES US DIFFERENT?</h2>

<div class="abs photo" style="left:119px;top:2333px;width:268px;height:268px;background:linear-gradient(135deg,#f3f6f8,#cdd6dc 60%,#7f8a90)" role="img" aria-label="Dental surgery with treatment chair"></div>
<div class="abs photo" style="left:461px;top:2333px;width:268px;height:268px;background:linear-gradient(135deg,#8a7a6a,#d7d9da 50%,#9aa3a8)" role="img" aria-label="Close view of a dental chair headrest"></div>
<div class="abs photo" style="left:822px;top:2333px;width:268px;height:268px;background:var(--white);display:flex;align-items:center;justify-content:center">
  <span style="font-family:'Lato',sans-serif;font-weight:700;font-size:54px;color:var(--brand)">Brivo</span>
</div>

<h3 class="abs h3" style="left:53px;top:2628px;width:400px;font-size:27px">OUR STORY</h3>
<p class="abs body" style="left:103px;top:2680px;width:300px">Dr Helena Marsh and her team believes everyone deserves a beautiful Smile, whoever and where ever you may be.</p>

<h3 class="abs h3" style="left:395px;top:2628px;width:400px;font-size:27px">OUR MISSION</h3>
<p class="abs body" style="left:440px;top:2682px;width:310px">At Brivo we aim to put a beautiful Smile on your face. &nbsp;Our dedicated team of Professionals aim to deliver the best possible Dental Care</p>

<h3 class="abs h3" style="left:756px;top:2628px;width:400px;font-size:27px">OUR TEAM</h3>
<p class="abs body" style="left:800px;top:2680px;width:312px">At Brivo, our team consists of qualified and trained Dentists, Therapists and Nurses with over a decade of experience in the industry.</p>

<section class="abs map" role="img" aria-label="Street map showing the clinic location"></section>
<div class="abs contact-frame"></div>
<div class="abs contact">
  <h4>CONTACT INFO</h4>
  <ul>
    <li><svg width="12" height="14" viewBox="0 0 12 14"><path d="M6 0a5 5 0 0 0-5 5c0 4 5 9 5 9s5-5 5-9a5 5 0 0 0-5-5zm0 7a2 2 0 1 1 0-4 2 2 0 0 1 0 4z" fill="#fff"/></svg>27 Kessel St, Marlow NSW 2600, Australia</li>
    <li><svg width="13" height="13" viewBox="0 0 24 24"><path d="M6.6 10.8a15 15 0 0 0 6.6 6.6l2.2-2.2c.3-.3.7-.4 1-.2 1.1.4 2.3.6 3.6.6.6 0 1 .4 1 1V20c0 .6-.4 1-1 1A17 17 0 0 1 3 4c0-.6.4-1 1-1h3.5c.6 0 1 .4 1 1 0 1.3.2 2.5.6 3.6.1.3 0 .7-.2 1z" fill="#fff"/></svg>+0400 555 219</li>
    <li><svg width="13" height="11" viewBox="0 0 13 11"><rect width="13" height="11" rx="1" fill="#fff"/><path d="M0 1l6.5 5L13 1" stroke="#0392cd" fill="none"/></svg>hello@brivo.com.au</li>
    <li><svg width="13" height="13" viewBox="0 0 14 14"><circle cx="7" cy="7" r="7" fill="#fff"/><path d="M7 3v4h3" stroke="#0392cd" stroke-width="1.5" fill="none"/></svg>Monday to Friday 8am to 4pm</li>
  </ul>
</div>

<footer class="abs footer">
  <nav><span>Home</span><span>Services</span><span>About Us</span><span>News</span><span>Contact us</span></nav>
  <p>Copyright © 2019 Brivo-dental . All Rights Reserved.</p>
</footer>

</body>
</html>
```